indépendant en tant que Massothérapeute et Préparateur Mental, j'ai besoin de ...

Massothérapeute et préparateur mental indépendant, je recherche une carte de visite sobre et dynamique, sans images liées au massage ou à la préparation mentale mais intégrant mon logo. Les couleurs que j'aime bien sont : Blanc, gris, anthracite, noir et jaune

Contact Information for Business Card

carte de préférence Horizontale
neutre qui puisse toucher le deux domaines Massothérapie et préparation mentale

Requirements
Must have
• mon projet doit intégrer au recto:
LOGO
Loïc Bardèze
078 513 26 48
info@loicbardeze.ch
et éventuellement www.loicbardeze.ch

et au verso les deux adresses:

Chemin des Ormilles 7B
1400 Yverdon-les-Bains

Route de la Gravière 9
1700 Fribourg

Should not have
• mon projet ne doit pas contenir d'image en liens avec le massage ni la préparation mentale.

```html
<!DOCTYPE html>
<html lang="fr">
<head>
<meta charset="utf-8">
<title>Loïc Bardèze — Carte de visite</title>
<link rel="stylesheet" href="https://fonts.googleapis.com/css2?family=Roboto:wght@300;400;700&display=swap">
<style>
  :root {
    --backdrop: #d9d9d9;
    --card: #1f1c1d;
    --ink: #e6e6e6;
    --ink-soft: #bdbdbd;
    --rule: #8a8a8a;
    --silver: #c9bfc2;
    --gloss: #0d0c0c;
  }
  * { box-sizing: border-box; margin: 0; padding: 0; }
  html, body { width: 1200px; height: 800px; overflow: hidden; }
  body {
    background: var(--backdrop);
    font-family: "Roboto", Arial, sans-serif;
    color: var(--ink);
    position: relative;
  }
  .card {
    position: absolute;
    top: 236px;
    width: 540px;
    height: 327px;
    background: var(--card);
    border-radius: 22px;
    overflow: hidden;
  }
  .card--front { left: 40px; }
  .card--back  { left: 620px; }

  /* Front side */
  .brand {
    position: absolute;
    top: 40px;
    right: 40px;
    text-align: right;
  }
  .brand__name {
    font-size: 30px;
    font-weight: 700;
    letter-spacing: 0.5px;
    color: var(--ink);
    display: flex;
    align-items: center;
    justify-content: flex-end;
    gap: 10px;
  }
  .brand__dot {
    width: 12px; height: 12px; border-radius: 50%;
    background: var(--ink);
  }
  .brand__tagline {
    margin-top: 4px;
    font-size: 13px;
    font-weight: 400;
    font-variant: small-caps;
    letter-spacing: 1px;
    color: var(--ink-soft);
  }
  .divider-top {
    position: absolute;
    top: 126px;
    right: 40px;
    width: 200px;
    height: 1px;
    background: var(--rule);
  }
  .addresses {
    position: absolute;
    top: 142px;
    right: 40px;
    text-align: right;
    font-size: 13px;
    font-weight: 300;
    line-height: 1.4;
    color: var(--ink-soft);
  }
  .addresses p + p { margin-top: 14px; }

  .owner {
    position: absolute;
    left: 40px;
    bottom: 112px;
    display: flex;
    align-items: center;
    gap: 10px;
    width: 300px;
  }
  .owner__name { font-size: 17px; font-weight: 700; white-space: nowrap; }
  .owner__rule { flex: 1; height: 1px; background: var(--rule); }

  .contacts {
    position: absolute;
    left: 40px;
    bottom: 34px;
    list-style: none;
    font-size: 13.5px;
    font-weight: 300;
    line-height: 22px;
  }
  .contacts li { display: flex; align-items: center; gap: 10px; }
  .contacts svg { width: 11px; height: 11px; fill: var(--ink); flex: none; }

  /* Back side */
  .back-brand {
    position: absolute;
    left: 0; right: 0;
    top: 118px;
    text-align: center;
  }
  .back-brand__name {
    font-size: 44px;
    font-weight: 700;
    color: var(--silver);
    display: inline-flex;
    align-items: center;
    gap: 14px;
  }
  .back-brand__dot {
    width: 16px; height: 16px; border-radius: 50%;
    background: var(--silver);
  }
  .back-brand__tagline {
    margin-top: 6px;
    font-size: 14px;
    font-variant: small-caps;
    letter-spacing: 1.2px;
    color: var(--gloss);
  }
</style>
</head>
<body>

<section class="card card--front" aria-label="Recto">
  <header class="brand">
    <div class="brand__name"><span class="brand__dot"></span>Loïc Bardèze</div>
    <div class="brand__tagline">Massothérapeute / Préparateur Mental</div>
  </header>

  <div class="divider-top"></div>
  <address class="addresses" style="font-style:normal">
    <p>Route de la Gravière 9<br>1700 Fribourg</p>
    <p>Chemin des Ormilles 7B<br>1400 Yverdon-les-Bains</p>
  </address>

  <div class="owner">
    <span class="owner__name">Loïc Bardèze</span>
    <span class="owner__rule"></span>
  </div>

  <ul class="contacts">
    <li>
      <svg viewBox="0 0 16 16" aria-hidden="true"><path d="M3.5 1l2.5 3-1.5 2c1 2 3 4 5 5l2-1.5 3 2.5-1.5 2.5C7 15 1 9 1 2.5z"/></svg>
      078 513 26 48
    </li>
    <li>
      <svg viewBox="0 0 16 16" aria-hidden="true"><path d="M1 3h14v10H1z M2 4l6 5 6-5" fill="none" stroke="#e6e6e6" stroke-width="1.6"/></svg>
      info@loicbardeze.ch
    </li>
    <li>
      <svg viewBox="0 0 16 16" aria-hidden="true"><circle cx="8" cy="8" r="7"/><path d="M1 8h14M8 1c3 3 3 11 0 14M8 1c-3 3-3 11 0 14" fill="none" stroke="#1f1c1d" stroke-width="1.2"/></svg>
      www.loicbardeze.ch
    </li>
  </ul>
</section>

<section class="card card--back" aria-label="Verso">
  <div class="back-brand">
    <div class="back-brand__name"><span class="back-brand__dot"></span>Loïc Bardèze</div>
    <div class="back-brand__tagline">Massothérapeute / Préparateur Mental</div>
  </div>
</section>

</body>
</html>
```